Fabric Store Business card

Need a business card portraying store logo and up and coming business of quilt fabrics, apparel fabrics, notions and buttons. Our business name is Gilded Thimble and Beyond. Am attaching logo. The design should communicate a growing business and warm atmosphere. Would like address and store hours and contact info displayed on card. Mon - Fri 9:30 to 5:00, Saturday 9:30 to 1:00. Address 784 W Orchard Ave, Newton, KS 67230 email: gildedthimblebeyond@mailvexa.com. Phone and fax 316-527-3486. After hours contact # 620-431-9052 Also like vintage sewing machines and dress forms if it works to incorporate fine, if not thats ok too.
Store

```html
<!DOCTYPE html>
<html lang="en">
<head>
<meta charset="utf-8">
<title>Gilded Thimble and Beyond – Business Card</title>
<link href="https://fonts.googleapis.com/css2?family=Oswald:wght@400;500&family=Roboto+Condensed:wght@400;700&display=swap" rel="stylesheet">
<style>
  :root {
    --backdrop: #e7e4e1;
    --card-white: #ffffff;
    --card-shade: #f1f1f1;
    --brand-red: #9c2e39;
    --ink-white: #ffffff;
    --ink-soft: #f3dcdf;
  }
  * { margin: 0; padding: 0; box-sizing: border-box; }
  html, body { width: 1200px; height: 896px; overflow: hidden; }
  body {
    background: var(--backdrop);
    position: relative;
    font-family: "Roboto Condensed", "Arial Narrow", sans-serif;
  }
  .card {
    position: absolute;
    left: 250px;
    width: 700px;
    height: 400px;
    background: linear-gradient(160deg, var(--card-white) 40%, var(--card-shade));
    box-shadow: 0 6px 18px rgba(0,0,0,0.18);
    overflow: hidden;
  }
  .card--front { top: 30px; }
  .card--back { top: 466px; }

  .brand {
    position: absolute;
    display: flex;
    align-items: center;
    gap: 16px;
  }
  .brand__dot {
    width: 46px; height: 46px;
    border-radius: 50%;
    background: var(--brand-red);
    flex: none;
  }
  .brand__name {
    font-weight: 400;
    font-size: 34px;
    line-height: 1.05;
    color: var(--brand-red);
  }
  .card--front .brand { left: 120px; top: 105px; }

  .front-band__rule {
    position: absolute; left: 0; right: 0;
    top: 272px; height: 4px;
    background: var(--brand-red);
  }
  .front-band {
    position: absolute; left: 0; right: 0; bottom: 0;
    height: 116px;
    background: var(--brand-red);
  }
  .front-band__inner-line {
    position: absolute; left: 0; right: 0;
    top: 8px; height: 3px;
    background: var(--ink-white);
  }

  .card--back .brand { left: 40px; top: 170px; }
  .contact-panel {
    position: absolute;
    top: 0; right: 0; bottom: 0;
    width: 340px;
    background: var(--brand-red);
    color: var(--ink-white);
    padding: 40px 24px 0 34px;
  }
  .contact-panel__name {
    font-family: "Oswald", "Arial Narrow", sans-serif;
    font-weight: 500;
    font-size: 36px;
    letter-spacing: 3px;
    text-transform: uppercase;
    line-height: 1;
  }
  .contact-panel__title {
    font-size: 14px;
    letter-spacing: 2px;
    text-transform: uppercase;
    color: var(--ink-soft);
    margin-top: 4px;
  }
  .contact-panel__address {
    font-size: 19px;
    line-height: 1.35;
    letter-spacing: 0.5px;
    margin-top: 24px;
  }
  .contact-list {
    list-style: none;
    margin-top: 14px;
  }
  .contact-list__item {
    display: flex;
    align-items: center;
    gap: 12px;
    font-size: 15px;
    letter-spacing: 0.2px;
    height: 28px;
    white-space: nowrap;
  }
  .contact-list__label {
    color: var(--ink-soft);
    font-size: 13px;
    text-transform: uppercase;
    letter-spacing: 1px;
    margin-right: 6px;
  }
  .contact-list__icon {
    width: 20px; height: 20px;
    flex: none;
    background: var(--ink-white);
    border-radius: 3px;
    display: flex; align-items: center; justify-content: center;
  }
  .contact-list__icon svg { width: 14px; height: 14px; }
  .store-hours {
    margin-top: 14px;
    padding-top: 10px;
    border-top: 1px solid rgba(255,255,255,0.35);
    font-size: 14px;
    line-height: 1.4;
    letter-spacing: 0.3px;
  }
  .store-hours__label {
    font-weight: 700;
    text-transform: uppercase;
    letter-spacing: 1px;
    font-size: 13px;
    margin-right: 6px;
  }
</style>
</head>
<body>

  <section class="card card--front" aria-label="Business card front">
    <div class="brand">
      <span class="brand__dot"></span>
      <span class="brand__name">Gilded Thimble<br>and Beyond</span>
    </div>
    <div class="front-band__rule"></div>
    <div class="front-band">
      <div class="front-band__inner-line"></div>
    </div>
  </section>

  <section class="card card--back" aria-label="Business card back">
    <div class="brand">
      <span class="brand__dot"></span>
      <span class="brand__name">Gilded Thimble<br>and Beyond</span>
    </div>

    <div class="contact-panel">
      <h1 class="contact-panel__name">Mara Ellison</h1>
      <p class="contact-panel__title">General Manager</p>
      <p class="contact-panel__address">784 W Orchard Ave<br>Newton, KS 67230</p>
      <ul class="contact-list">
        <li class="contact-list__item">
          <span class="contact-list__icon">
            <svg viewBox="0 0 24 24"><path fill="#9c2e39" d="M6.6 10.8a15 15 0 0 0 6.6 6.6l2.2-2.2a1 1 0 0 1 1-.25 11.4 11.4 0 0 0 3.6.57 1 1 0 0 1 1 1V20a1 1 0 0 1-1 1A17 17 0 0 1 3 4a1 1 0 0 1 1-1h3.5a1 1 0 0 1 1 1c0 1.25.2 2.45.57 3.57a1 1 0 0 1-.25 1z"/></svg>
          </span>
          <span><span class="contact-list__label">Phone / Fax</span>316-527-3486</span>
        </li>
        <li class="contact-list__item">
          <span class="contact-list__icon">
            <svg viewBox="0 0 24 24"><path fill="#9c2e39" d="M6.6 10.8a15 15 0 0 0 6.6 6.6l2.2-2.2a1 1 0 0 1 1-.25 11.4 11.4 0 0 0 3.6.57 1 1 0 0 1 1 1V20a1 1 0 0 1-1 1A17 17 0 0 1 3 4a1 1 0 0 1 1-1h3.5a1 1 0 0 1 1 1c0 1.25.2 2.45.57 3.57a1 1 0 0 1-.25 1z"/></svg>
          </span>
          <span><span class="contact-list__label">After Hours</span>620-431-9052</span>
        </li>
        <li class="contact-list__item">
          <span class="contact-list__icon">
            <svg viewBox="0 0 24 24"><rect x="2" y="5" width="20" height="14" rx="1.5" fill="#9c2e39"/><path d="M3 6l9 7 9-7" fill="none" stroke="#fff" stroke-width="1.8"/></svg>
          </span>
          gildedthimblebeyond@mailvexa.com
        </li>
        <li class="contact-list__item">
          <span class="contact-list__icon">
            <svg viewBox="0 0 24 24"><circle cx="12" cy="12" r="9" fill="none" stroke="#9c2e39" stroke-width="2"/><path d="M3 12h18M12 3c3 3 3 15 0 18M12 3c-3 3-3 15 0 18" fill="none" stroke="#9c2e39" stroke-width="1.6"/></svg>
          </span>
          www.gildedthimblebeyond.com
        </li>
      </ul>
      <p class="store-hours">
        <span class="store-hours__label">Hours</span>Mon–Fri 9:30–5:00 · Sat 9:30–1:00
      </p>
    </div>
  </section>

</body>
</html>
```